Flyer-Design für psychologische Beratungspraxis für Mütter
Vielen herzlichen Dank! Super Kommunikation, alle Änderungswünsche wurden sofort umgesetzt, auch hin und her meinerseits war kein Problem, immer wieder. Schnelle Reaktion, tolle Ideen. Ich bin super zufrieden und würde jederzeit sehr gerne wieder mit brightfoxes zusammenarbeiten! Toller Flyer, ich liebe meinen neuen Flyer! :)
Zielgruppe
Gelassenheitswerkstatt ist eine psychologische Beratungspraxis. Ich unterstütze Mütter, Schwangere und Frauen mit Kinderwunsch bei Herausforderungen rund um Schwangerschaft, Geburt, Mutterschaft, und damit einhergehenden Problemen.
Aufgabenstellung
Text nochmal geringgradig geändert...siehe Datei anbei

```html
<!DOCTYPE html>
<html lang="de">
<head>
<meta charset="utf-8">
<title>Flyer – Beratung für Mütter</title>
<link href="https://fonts.googleapis.com/css2?family=Arimo:wght@400;700&display=swap" rel="stylesheet">
<style>
  :root {
    --backdrop: #e4ebe4;
    --paper: #ffffff;
    --paper-warm: #fbf9da;
    --ink: #2b2d7c;
    --accent-green: #3d9e32;
    --band: #e5e5f1;
  }
  html, body {
    margin: 0;
    width: 1200px;
    height: 1200px;
    overflow: hidden;
    background: var(--backdrop);
    font-family: "Arimo", Arial, sans-serif;
    color: var(--ink);
  }
  .flyer-page {
    position: absolute;
    left: 48px;
    top: 48px;
    width: 1106px;
    height: 1106px;
    background: linear-gradient(to bottom, var(--paper) 0%, var(--paper) 35%, var(--paper-warm) 100%);
    box-shadow: 0 2px 10px rgba(0,0,0,0.18);
    overflow: hidden;
  }
  .column {
    position: absolute;
    top: 36px;
    font-size: 20px;
    line-height: 31px;
  }
  .column p { margin: 0; }
  .column-intro {
    left: 42px;
    width: 470px;
    text-align: justify;
  }
  .column-questions {
    left: 594px;
    width: 470px;
  }
  .lead { color: var(--accent-green); font-weight: 700; }
  strong { font-weight: 700; }
  .column-intro p + p { margin-top: 0; }
  .gap-lg { margin-top: 31px !important; }
  .question { margin-top: 17px !important; }
  .question.first { margin-top: 31px !important; }
  .question.after-indent { margin-top: 17px !important; }
  .indent { padding-left: 62px; }
  .underlined { text-decoration: underline; text-underline-offset: 3px; }
  .brush-edge {
    position: absolute;
    left: 0;
    top: 852px;
    width: 1106px;
    height: 10px;
  }
  .closing-band {
    position: absolute;
    left: 0;
    top: 858px;
    width: 1106px;
    height: 248px;
    background: var(--band);
    box-sizing: border-box;
    padding: 22px 40px 0;
    text-align: center;
    font-size: 20px;
    line-height: 29px;
  }
  .closing-band p { margin: 0 0 12px; }
</style>
</head>
<body>
<main class="flyer-page">
  <section class="column column-intro">
    <p><span class="lead">Mutter sein ist wunderbar.</span> Wenn eine Frau Mutter wird, ist sie plötzlich verliebt über beide Ohren, unbändig stolz und von Glücksgefühlen völlig überwältigt.</p>
    <p class="gap-lg lead">So ist es doch „NORMAL“, oder...?</p>
    <p class="gap-lg"><strong>Überforderung, Frustration und Verzweiflung</strong> kennen Mütter, Frauen mit Kinderwunsch und werdende Mütter allerdings ebenfalls nur zu gut. Wichtig ist, dass die Beurteilung einer Situation, d.h. wie stark sie uns belastet, allein uns selbst zusteht.</p>
    <p>Nur unsere eigene <strong>subjektive Einschätzung</strong> ist ausschlaggebend.</p>
    <p class="gap-lg">So unterschiedlich wir Menschen sind, so verschieden ist auch unser persönliches Fühlen und Erleben. Für unsere Herausforderungen benötigen wir deshalb <strong>individuell passende Lösungen.</strong></p>
    <p class="gap-lg">Ja, Mutter sein ist wundervoll! Und ja, die Dynamik der Paarbeziehung verändert sich schlagartig und wir stehen plötzlich vor einer der <strong>erfüllendsten Aufgaben</strong> und zugleich einer der größten <strong>existentiellen Herausforderungen,</strong> die uns das Leben bietet: Eltern sein.</p>
  </section>

  <section class="column column-questions">
    <p class="lead">Was also wenn...</p>
    <p class="question first">..wir <strong>gern Mutter wären</strong> aber das Leben andere Pläne hat?</p>
    <p class="question first">...uns die Erfahrung der <strong>Geburt belastet,</strong> aber niemand zuhört, weil ja</p>
    <p class="indent">„jetzt alles ok sei“?</p>
    <p class="question after-indent">...wir unser <strong>Kind verloren</strong> haben?</p>
    <p class="question">...wir uns treu bleiben wollen aber uns dennoch durch die Meinung anderer <strong>verunsichern</strong> lassen?</p>
    <p class="question">...wir eben <strong>nicht stolz</strong> darauf sind, wie wir den letzten Schreianfall unseres Babys begleitet haben?</p>
    <p class="question">...wir weder die <strong>Wut</strong> unseres Kindes, noch unsere eigene Wut gebändigt bekommen?</p>
    <p class="question">...unser Kind oder wir selbst mit einer <strong>Krankheit</strong> zu kämpfen haben?</p>
    <p class="question">...wir selbst oder unser Partner uns <strong>kaum wiedererkennen?</strong></p>
    <p class="question">...wir mit der Situation <strong>überfordert</strong> sind, und nicht <strong class="underlined">mehr weiter wissen</strong><strong>?</strong></p>
  </section>

  <svg class="brush-edge" viewBox="0 0 1106 10" preserveAspectRatio="none" aria-hidden="true">
    <path d="M0 3 L120 2 L260 4 L420 1.5 L580 3.5 L740 2 L900 4 L1106 2.5 L1106 8 L950 7 L800 8.5 L640 6.5 L480 8 L320 6.5 L160 8 L0 7 Z" fill="var(--accent-green)"/>
  </svg>

  <section class="closing-band">
    <p>Um <strong>trotz Rückschlägen ein zufriedenes Leben zu führen</strong> und um feinfühlig für unsere Kinder da zu sein, benötigen wir viel Kraft.</p>
    <p>Mentale Kraft, die es uns ermöglicht aus den Augen unserer Kinder zu sehen, unsere eigenen Gefühle zu regulieren und die starken Gefühle unserer Kinder auszuhalten und zu begleiten.</p>
    <p>Gemeinsam erarbeiten wir <strong>individuelle Strategien,</strong> wie Sie auf Ihre eigenen Ressourcen besser zugreifen, und so <strong class="underlined">mental gestärkt nach vorne schauen können.</strong></p>
  </section>
</main>
</body>
</html>
```